Coffeeshop menu for filter tip

We want to have a cannabis (coffeeshop) menu in the size 25mm wide x 60mm wide. Some examples attached.

it must have the following text:
Menu

WEED p/g
Oblivane €16
Cloudplum €14
Tide Runner €14
Quincefig €16
Mega Marsh €14
Grey Heron €14

HASH p/g
Tashar Amber €12
Pebble Frost€11
Lime Dunes €14
Ash Petal €10

Target Market(s)

tourist in Amsterdam

Requirements
Nice to have
• cannabis sign leaf
• No Cigarettes allowed symbol

```html
<!DOCTYPE html>
<html lang="en">
<head>
<meta charset="utf-8">
<title>Coffeeshop Menu – Two Versions</title>
<link rel="stylesheet" href="https://fonts.googleapis.com/css2?family=PT+Serif:wght@400;700&family=PT+Sans+Narrow:wght@400;700&family=Archivo+Narrow:wght@700&display=swap">
<style>
  :root{
    --gold:#d4a75a;
    --gold-light:#e9cf9a;
    --paper:#e6e6e6;
    --ink:#111111;
    --bloom:#f7d44a;
    --leaf:#bdbdbd;
    --red:#e0141b;
    --white:#ffffff;
  }
  *{margin:0;padding:0;box-sizing:border-box}
  html,body{width:1200px;height:781px;overflow:hidden;background:var(--white)}
  body{position:relative;font-family:"PT Sans Narrow",sans-serif;color:var(--ink)}

  .menu-card{position:absolute;top:87px;width:254px;height:608px;background:var(--paper);overflow:hidden}
  .menu-card--classic{left:241px}
  .menu-card--banner{left:682px;top:88px}

  .abs{position:absolute}

  .section-title{position:absolute;font-family:"PT Serif",serif;font-weight:700;font-size:27px;line-height:1;color:var(--ink)}
  .section-title sup{font-size:13px;vertical-align:top;position:relative;top:-2px;margin-left:6px}

  .price-list{position:absolute;list-style:none}
  .price-row{display:flex;justify-content:space-between;align-items:flex-end;border-bottom:1.5px solid var(--ink);height:29px;padding:0 4px 1px 9px}
  .price-row--tall{height:30px}
  .price-row--wide{height:35px}
  .item-name{font-size:23px;line-height:1}
  .item-price{font-size:27px;line-height:1}
  .item-price .euro{font-size:18px;margin-right:7px}
  .price-row.last{border-bottom:none}

  .title-ornament{position:absolute}

  .no-smoking{display:flex;align-items:center;gap:6px}
  .no-smoking-label{font-family:"Archivo Narrow",sans-serif;font-weight:700;font-size:17px;color:var(--red)}
</style>
</head>
<body>

<!-- Version A: classic -->
<section class="menu-card menu-card--classic" aria-label="Coffeeshop menu, classic layout">
  <div class="abs" role="img" aria-label="Soft yellow floral flourish background" style="left:0;top:60px;width:200px;height:440px;background:radial-gradient(ellipse at 40% 60%, rgba(247,212,74,.55), rgba(247,212,74,.15) 55%, rgba(230,230,230,0) 75%)"></div>
  <div class="abs" role="img" aria-label="Grey cannabis leaf silhouettes" style="left:0;top:450px;width:254px;height:96px;background:linear-gradient(180deg, rgba(189,189,189,0) 0%, rgba(189,189,189,.6) 100%)"></div>

  <svg class="abs" style="left:4px;top:21px" width="236" height="40" aria-hidden="true"><polygon points="0,0 236,0 218,40 0,40" fill="var(--gold)"/></svg>
  <h2 class="section-title" style="left:18px;top:29px">WEED<sup>p/g</sup></h2>

  <ul class="price-list" style="left:12px;top:68px;width:236px">
    <li class="price-row"><span class="item-name">Oblivane</span><span class="item-price"><span class="euro">€</span>16</span></li>
    <li class="price-row"><span class="item-name">Cloudplum</span><span class="item-price"><span class="euro">€</span>16</span></li>
    <li class="price-row"><span class="item-name">Tide Runner</span><span class="item-price"><span class="euro">€</span>14</span></li>
    <li class="price-row"><span class="item-name">Quincefig</span><span class="item-price"><span class="euro">€</span>16</span></li>
    <li class="price-row"><span class="item-name">Mega Marsh</span><span class="item-price"><span class="euro">€</span>14</span></li>
    <li class="price-row price-row--wide"><span class="item-name">Grey Heron</span><span class="item-price"><span class="euro">€</span>14</span></li>
  </ul>

  <div class="title-ornament" role="img" aria-label="Ribbon title ornament for the city menu heading" style="left:10px;top:266px;width:236px;height:70px;background:linear-gradient(180deg, var(--gold) 0%, var(--gold-light) 100%);opacity:.75"></div>

  <svg class="abs" style="left:17px;top:359px" width="237" height="40" aria-hidden="true"><polygon points="0,0 237,0 237,40 18,40" fill="var(--gold)"/></svg>
  <h2 class="section-title" style="left:126px;top:367px">HASH<sup>p/g</sup></h2>

  <ul class="price-list" style="left:12px;top:411px;width:236px">
    <li class="price-row price-row--tall"><span class="item-name">Tashar Amber</span><span class="item-price"><span class="euro">€</span>12</span></li>
    <li class="price-row price-row--tall"><span class="item-name">Pebble Frost</span><span class="item-price"><span class="euro">€</span>11</span></li>
    <li class="price-row price-row--tall"><span class="item-name">Lime Dunes</span><span class="item-price"><span class="euro">€</span>14</span></li>
    <li class="price-row price-row--tall last"><span class="item-name">Ash Petal</span><span class="item-price"><span class="euro">€</span>10</span></li>
  </ul>

  <footer class="abs no-smoking" style="left:0;top:546px;width:254px;height:62px;background:var(--gold);justify-content:center">
    <svg width="44" height="44" viewBox="0 0 44 44" role="img" aria-label="No smoking symbol">
      <circle cx="22" cy="22" r="19" fill="var(--white)" stroke="var(--red)" stroke-width="4"/>
      <rect x="8" y="20" width="24" height="5" fill="#8a8a8a"/>
      <rect x="32" y="20" width="4" height="5" fill="var(--ink)"/>
      <line x1="9" y1="9" x2="35" y2="35" stroke="var(--red)" stroke-width="4"/>
    </svg>
    <span class="no-smoking-label">NO SIGARETS</span>
  </footer>
</section>

<!-- Version B: banner -->
<section class="menu-card menu-card--banner" aria-label="Coffeeshop menu, banner layout">
  <svg class="abs" style="left:0;top:0" width="254" height="140" aria-hidden="true">
    <path d="M0,0 H254 V112 Q170,100 127,137 Q84,100 0,112 Z" fill="var(--gold)"/>
  </svg>
  <div class="title-ornament" role="img" aria-label="Scroll ribbon with flourishes for the city menu heading" style="left:22px;top:16px;width:210px;height:80px;background:radial-gradient(ellipse at 50% 45%, rgba(255,255,255,.85), rgba(233,207,154,.6) 55%, rgba(212,167,90,0) 80%)"></div>

  <div class="abs" style="left:0;top:150px;width:146px;height:30px;background:var(--gold)"></div>
  <h2 class="section-title" style="left:6px;top:153px">WEED<sup>p/g</sup></h2>

  <ul class="price-list" style="left:6px;top:178px;width:236px">
    <li class="price-row"><span class="item-name">Oblivane</span><span class="item-price"><span class="euro">€</span>16</span></li>
    <li class="price-row"><span class="item-name">Cloudplum</span><span class="item-price"><span class="euro">€</span>16</span></li>
    <li class="price-row"><span class="item-name">Tide Runner</span><span class="item-price"><span class="euro">€</span>14</span></li>
    <li class="price-row"><span class="item-name">Quincefig</span><span class="item-price"><span class="euro">€</span>16</span></li>
    <li class="price-row"><span class="item-name">Mega Marsh</span><span class="item-price"><span class="euro">€</span>14</span></li>
    <li class="price-row price-row--wide"><span class="item-name">Grey Heron</span><span class="item-price"><span class="euro">€</span>14</span></li>
  </ul>

  <div class="abs" style="left:100px;top:374px;width:154px;height:32px;background:var(--gold)"></div>
  <h2 class="section-title" style="left:142px;top:378px">HASH<sup>p/g</sup></h2>

  <ul class="price-list" style="left:10px;top:411px;width:232px">
    <li class="price-row price-row--tall"><span class="item-name">Tashar Amber</span><span class="item-price"><span class="euro">€</span>12</span></li>
    <li class="price-row price-row--tall"><span class="item-name">Pebble Frost</span><span class="item-price"><span class="euro">€</span>11</span></li>
    <li class="price-row price-row--tall"><span class="item-name">Lime Dunes</span><span class="item-price"><span class="euro">€</span>14</span></li>
    <li class="price-row price-row--tall last"><span class="item-name">Ash Petal</span><span class="item-price"><span class="euro">€</span>10</span></li>
  </ul>

  <footer class="abs no-smoking" style="left:6px;top:540px;width:180px;height:60px;background:var(--gold);border-radius:18px 30px 22px 26px;padding-left:32px">
    <svg width="40" height="40" viewBox="0 0 44 44" role="img" aria-label="No smoking symbol">
      <circle cx="22" cy="22" r="19" fill="var(--white)" stroke="var(--red)" stroke-width="4"/>
      <rect x="8" y="20" width="24" height="5" fill="#8a8a8a"/>
      <rect x="32" y="20" width="4" height="5" fill="var(--ink)"/>
      <line x1="9" y1="9" x2="35" y2="35" stroke="var(--red)" stroke-width="4"/>
    </svg>
    <span class="no-smoking-label" style="font-size:14px">NO SIGARETS</span>
  </footer>

  <svg class="abs" style="left:208px;top:560px" width="46" height="48" aria-hidden="true">
    <polygon points="46,0 46,48 4,48" fill="var(--ink)"/>
    <path d="M46,0 Q20,14 4,48 Q0,20 46,0 Z" fill="var(--white)"/>
  </svg>
</section>

</body>
</html>
```